Advertisement Design

I'm looking for a post card sized advertisement piece that I will be dropping off to commercial and residential customers.
On one side I want it promoting carpet cleaning services and on the other side dryer vent cleaning services.
I've uploaded two different layouts of my company logo for you to choice from.
One batch will be printed with my Michigan Number
One batch will be printed with my Tennessee number
Will share contact numbers with the winner so just use a make up number
742-318-9516

```html
<!DOCTYPE html>
<html lang="en">
<head>
<meta charset="utf-8">
<title>Pile Pilot – Carpet Cleaning Postcard</title>
<link rel="stylesheet" href="https://fonts.googleapis.com/css2?family=Montserrat:wght@300;500;600;700;800&family=Nunito:wght@800;900&display=swap">
<style>
  :root{
    --blue:#0a7cc1;
    --ink:#3c3c3e;
    --dark:#2b2b2d;
    --white:#ffffff;
    --divider:#5a5a5c;
  }
  *{box-sizing:border-box;margin:0;padding:0}
  html,body{width:1200px;height:941px;overflow:hidden;background:var(--white)}
  .card{position:relative;width:1200px;height:941px;background:var(--white);font-family:"Montserrat",sans-serif;color:var(--ink)}

  .brand{position:absolute;left:54px;top:62px;display:flex;flex-direction:column;align-items:flex-start}
  .brand-mark{width:80px;height:80px;background:var(--blue);border-radius:10px;margin-left:95px}
  .brand-name{margin-top:18px;font-family:"Montserrat",sans-serif;font-weight:700;font-size:38px;color:var(--blue);letter-spacing:1px}

  .headline{position:absolute;left:49px;top:256px;font-weight:800;font-size:52px;color:var(--blue);letter-spacing:-0.5px;line-height:1}
  .subhead{position:absolute;left:51px;top:326px;font-weight:300;font-size:36px;line-height:44px;color:var(--ink);text-transform:uppercase}
  .subhead strong{font-weight:800}

  .band{position:absolute;left:0;top:483px;width:1048px;height:301px;background:var(--dark);border-bottom-right-radius:14px}

  .photo{position:absolute;left:641px;top:51px;width:516px;height:565px;border-radius:30px;
    background:linear-gradient(180deg,#a9a8a6 0%,#bbbab8 45%,#d6d4d2 52%,#cfcdcb 70%,#bdbab7 100%)}

  .intro{position:absolute;left:50px;top:494px;width:520px;color:var(--white)}
  .intro h2{font-weight:800;font-size:32px;color:var(--blue);line-height:1;margin-bottom:8px}
  .intro p{font-size:13px;line-height:17px;font-weight:300}
  .intro p.lead{font-weight:700}

  .services{position:absolute;left:18px;top:636px;width:1020px;display:flex;list-style:none}
  .service{display:flex;flex-direction:column;align-items:center;text-align:center;font-family:"Nunito",sans-serif;font-weight:900;font-size:15.5px;line-height:20px;color:var(--white);border-right:1px dashed var(--divider);height:128px}
  .service:last-child{border-right:none}
  .service svg{width:42px;height:42px;margin-bottom:14px}

  .contacts{position:absolute;top:810px;display:flex;flex-direction:column;gap:8px}
  .contacts h3{font-weight:800;font-size:19px;color:var(--blue);margin-bottom:2px}
  .contacts .line{display:flex;align-items:center;gap:9px;font-weight:700;font-size:16px;color:var(--ink)}
  .contacts svg{width:15px;height:15px}
  .contacts.west{left:50px}
  .contacts.middle{left:387px}

  .website{position:absolute;left:695px;top:821px;width:505px;height:71px;background:var(--dark);border-top-left-radius:4px;border-bottom-left-radius:4px;
    color:var(--white);font-weight:800;font-size:34px;letter-spacing:2px;display:flex;align-items:center;padding-left:22px}
</style>
</head>
<body>
<div class="card">

  <div class="brand">
    <div class="brand-mark"></div>
    <div class="brand-name">Pile Pilot</div>
  </div>

  <h1 class="headline">CARPET CLEANING</h1>
  <p class="subhead">Providing services<br>for both <strong>residential</strong> &amp;<br><strong>commercial clients.</strong></p>

  <div class="band"></div>
  <div class="photo" role="img" aria-label="Photo of a carpet cleaning wand with a blue head resting on light grey carpet against a grey wall"></div>

  <section class="intro">
    <h2>CARPET CLEANING</h2>
    <p class="lead">At Pile Pilot, we have been providing carpet cleaning services for more than 40 years.</p>
    <p>Using state-of-the-art industrial equipment combined with our years of service, there is not much that we cannot clean.Carpet cleaning services include:</p>
  </section>

  <ul class="services">
    <li class="service" style="width:146px">
      <svg viewBox="0 0 42 42"><rect width="42" height="42" rx="3" fill="#0a7cc1"/><g fill="#fff"><rect x="12" y="11" width="18" height="22"/><rect x="9" y="33" width="24" height="2"/></g><g fill="#0a7cc1"><rect x="15" y="14" width="3" height="3"/><rect x="20" y="14" width="3" height="3"/><rect x="25" y="14" width="2" height="3"/><rect x="15" y="20" width="3" height="3"/><rect x="20" y="20" width="3" height="3"/><rect x="25" y="20" width="2" height="3"/><rect x="19" y="27" width="4" height="6"/></g></svg>
      Commercial<br>Carpet<br>Cleaning
    </li>
    <li class="service" style="width:137px">
      <svg viewBox="0 0 42 42"><rect width="42" height="42" rx="3" fill="#0a7cc1"/><path d="M8 21 21 9l13 12h-4v12H12V21z" fill="#fff"/><rect x="15" y="24" width="5" height="9" fill="#0a7cc1"/><rect x="23" y="23" width="6" height="5" fill="#0a7cc1"/></svg>
      Residential<br>Carpet<br>Cleaning
    </li>
    <li class="service" style="width:110px">
      <svg viewBox="0 0 42 42"><rect width="42" height="42" rx="3" fill="#0a7cc1"/><rect x="10" y="10" width="22" height="22" fill="none" stroke="#fff" stroke-width="2.5"/><rect x="15" y="15" width="12" height="12" fill="none" stroke="#fff" stroke-width="2"/><path d="M15 27 27 15" stroke="#fff" stroke-width="2"/></svg>
      Rug<br>Cleaning
    </li>
    <li class="service" style="width:150px">
      <svg viewBox="0 0 42 42"><rect width="42" height="42" rx="3" fill="#0a7cc1"/><path d="M7 24h28l-4 8H11z" fill="#fff"/><rect x="14" y="18" width="14" height="5" fill="#fff"/><rect x="20" y="9" width="2" height="9" fill="#fff"/><path d="M7 35q3-2 7 0t7 0 7 0 7 0" stroke="#fff" stroke-width="1.6" fill="none"/></svg>
      Boat, RV,<br>Aircraft<br>Carpet Cleaning
    </li>
    <li class="service" style="width:155px">
      <svg viewBox="0 0 42 42"><rect width="42" height="42" rx="3" fill="#0a7cc1"/><g stroke="#fff" stroke-width="3" fill="none" stroke-linecap="round"><path d="M13 32c-4-5 4-8 0-13s2-7 2-9"/><path d="M21 32c-4-5 4-8 0-13s2-7 2-9"/><path d="M29 32c-4-5 4-8 0-13s2-7 2-9"/></g></svg>
      Tile &amp; Grout<br>cleaning
    </li>
    <li class="service" style="width:164px">
      <svg viewBox="0 0 42 42"><rect width="42" height="42" rx="3" fill="#0a7cc1"/><path d="M8 10 14 14v18l-6 3zM34 10l-6 4v18l6 3z" fill="#fff"/><rect x="14" y="14" width="14" height="18" fill="none" stroke="#fff" stroke-width="2"/><rect x="18" y="18" width="6" height="14" fill="#fff"/></svg>
      Corridor Carpet<br>Cleaning
    </li>
    <li class="service" style="width:158px">
      <svg viewBox="0 0 42 42"><rect width="42" height="42" rx="3" fill="#0a7cc1"/><path d="M12 14q9-5 18 0v7H12z" fill="#fff"/><path d="M8 20h5v5h16v-5h5v9H8z" fill="#fff"/><rect x="10" y="29" width="3" height="4" fill="#fff"/><rect x="29" y="29" width="3" height="4" fill="#fff"/></svg>
      Upholstery<br>Cleaning
    </li>
  </ul>

  <div class="contacts west">
    <h3>WEST MICHIGAN</h3>
    <div class="line"><svg viewBox="0 0 16 16"><path d="M3 1l3 3-2 2c1 2 3 4 6 6l2-2 3 3-2 2C7 15 1 9 1 3z" fill="#0a7cc1"/></svg>742-318-9516</div>
    <div class="line"><svg viewBox="0 0 16 16"><rect x="1" y="3" width="14" height="10" fill="#0a7cc1"/><path d="M1 3l7 6 7-6" stroke="#fff" stroke-width="1.2" fill="none"/></svg>BILLING@PILEPILOT.COM</div>
  </div>

  <div class="contacts middle">
    <h3>MIDDLE TENNESSEE</h3>
    <div class="line"><svg viewBox="0 0 16 16"><path d="M3 1l3 3-2 2c1 2 3 4 6 6l2-2 3 3-2 2C7 15 1 9 1 3z" fill="#0a7cc1"/></svg>(615) 555-0147</div>
    <div class="line"><svg viewBox="0 0 16 16"><rect x="1" y="3" width="14" height="10" fill="#0a7cc1"/><path d="M1 3l7 6 7-6" stroke="#fff" stroke-width="1.2" fill="none"/></svg>DANA@PILEPILOT.COM</div>
  </div>

  <div class="website">www.PilePilot.com</div>

</div>
</body>
</html>
```